Business Card Design Project

i need a bussines car design
Velora Clinical Hypnotherapy

Daniel Wexford
Psychotherapy & Hypnosis

84261937 /0427591628

back of the card appoinment space.

file was provided on a PDF, LOgo , use the blu colorsa as well , elegant, clear,

Target Market(s)

young professional, caucasian , young mothers.

Industry/Entity Type

Business

```html
<!DOCTYPE html>
<html lang="en">
<head>
<meta charset="utf-8">
<title>Velora Clinical Hypnotherapy – Business Card</title>
<link rel="stylesheet" href="https://fonts.googleapis.com/css2?family=Source+Sans+3:wght@400;600;700&display=swap">
<style>
  :root {
    --bg: #ecebe8;
    --card: #ffffff;
    --blue: #1273bd;
    --blue-light: #1a9ad6;
    --grey-text: #6f6f6f;
    --grey-wave: #8c8c8c;
    --photo-top: #f6f3ee;
    --photo-bottom: #e9d9c6;
  }
  * { margin: 0; padding: 0; box-sizing: border-box; }
  html, body { width: 1200px; height: 789px; overflow: hidden; }
  body {
    background: var(--bg);
    font-family: "Source Sans 3", "Myriad Pro", Arial, sans-serif;
    position: relative;
  }
  .card {
    position: absolute;
    top: 130px;
    width: 317px;
    height: 561px;
    background: var(--card);
    border-radius: 20px;
    overflow: hidden;
    box-shadow: 0 6px 16px rgba(0,0,0,0.25);
    text-align: center;
  }
  .card--back { left: 279px; }
  .card--front { left: 664px; }
  .block { position: absolute; left: 0; width: 100%; }

  .back__title { top: 22px; color: var(--blue); font-weight: 700; font-size: 15px; }
  .back__contact { top: 43px; color: var(--grey-text); font-size: 14px; line-height: 20px; }
  .back__email { top: 85px; color: var(--grey-text); font-size: 11px; font-weight: 600; }
  .back__heading { top: 137px; color: var(--blue); font-weight: 700; font-size: 15px; }
  .appointments { top: 164px; list-style: none; color: var(--grey-text); font-size: 14px; }
  .appointments li { height: 35.6px; line-height: 22px; }
  .back__notice { top: 384px; color: var(--blue-light); font-size: 13px; line-height: 16.5px; padding: 0 46px; }
  .back__reg { top: 524px; color: #fff; font-size: 14px; }

  .wave { position: absolute; left: 0; bottom: 0; width: 100%; height: 90px; }

  .brand { top: 106px; color: var(--blue); font-size: 24px; font-weight: 400; letter-spacing: 0.3px; }
  .brand__url { top: 136px; color: #444; font-size: 9.5px; letter-spacing: 0.6px; }
  .brand__rule { position: absolute; top: 133px; left: 55px; width: 207px; height: 1px; background: var(--blue); }
  .person__name { top: 170px; color: var(--blue-light); font-size: 16px; }
  .person__role { top: 190px; color: var(--grey-text); font-size: 13px; }
  .photo {
    position: absolute;
    top: 225px; left: 57px;
    width: 206px; height: 265px;
    background: linear-gradient(180deg, var(--photo-top) 0%, var(--photo-top) 30%, var(--photo-bottom) 100%);
  }
  .front__phones { top: 518px; color: #fff; font-size: 13px; }
  .front__web { top: 535px; color: #fff; font-size: 15px; }
</style>
</head>
<body>

  <section class="card card--back" aria-label="Card back">
    <p class="block back__title">Velora Clinical Hypnotherapy</p>
    <p class="block back__contact">By Appointment . Phone: 0427 591 628<br>48 Corrigan St Elmhurst</p>
    <p class="block back__email">hello@veloraclinicalhypnotherapy.com.au</p>

    <h2 class="block back__heading">Your Appointments</h2>
    <ol class="block appointments">
      <li>1. _____am/pm _____________ ___/___/___</li>
      <li>2. _____am/pm _____________ ___/___/___</li>
      <li>3. _____am/pm _____________ ___/___/___</li>
      <li>4. _____am/pm _____________ ___/___/___</li>
      <li>5. _____am/pm _____________ ___/___/___</li>
    </ol>

    <p class="block back__notice">To reschedule your appointment, please SMS or phone 0427 591 628 at least 24 hours prior to your allocated time. Thank you.</p>

    <svg class="wave" viewBox="0 0 317 90" preserveAspectRatio="none" aria-hidden="true">
      <path d="M0 24 C90 8 200 0 317 6 L317 14 C210 12 110 20 0 40 Z" fill="var(--grey-wave)"/>
      <path d="M0 46 C110 22 220 14 317 18 L317 90 L0 90 Z" fill="var(--blue)"/>
    </svg>
    <p class="block back__reg">NHRA Registration No. NPM058214</p>
  </section>

  <section class="card card--front" aria-label="Card front">
    <p class="block brand">Velora Hypnotherapy</p>
    <span class="brand__rule"></span>
    <p class="block brand__url">www.veloraclinicalhypnotherapy.com.au</p>

    <p class="block person__name">Daniel Wexford</p>
    <p class="block person__role">Psychotherapy &amp; Hypnosis</p>

    <div class="photo" role="img" aria-label="Portrait photo of the practitioner in a light shirt, arms folded"></div>

    <svg class="wave" viewBox="0 0 317 90" preserveAspectRatio="none" aria-hidden="true">
      <path d="M0 24 C90 8 200 0 317 6 L317 14 C210 12 110 20 0 40 Z" fill="var(--grey-wave)"/>
      <path d="M0 46 C110 22 220 14 317 18 L317 90 L0 90 Z" fill="var(--blue)"/>
    </svg>
    <p class="block front__phones">84261937 /0427591628</p>
    <p class="block front__web">www.veloraclinicalhypnotherapy.com.au</p>
  </section>

</body>
</html>
```